Harborline Benches business cards

I’d like a business card design that includes my logo, a tag line and my contact info. Black, textured background. My contact info color should match the orange and blue gradients. Tagline under logo: “Wooden Tables and Furniture of the Highest Quality”

Target Market(s)

High end furniture buyers

Contact Information for Business Card

Contact info, logo and tagline

```html
<!DOCTYPE html>
<html lang="en">
<head>
<meta charset="UTF-8">
<title>Harborline Benches – Business Cards</title>
<link href="https://fonts.googleapis.com/css2?family=Open+Sans:wght@600&family=Poppins:wght@400;500&display=swap" rel="stylesheet">
<style>
  :root {
    --backdrop: #6e6e6e;
    --paper: #ffffff;
    --ink: #1c1c1c;
    --orange: #ec7424;
    --blue: #0a55ad;
    --rule: #c9c9c9;
    --night-1: #1b1e24;
    --night-2: #2c313b;
    --night-3: #20242b;
  }
  * { margin: 0; padding: 0; box-sizing: border-box; }
  html, body {
    width: 1093px; height: 1200px; overflow: hidden;
    background: var(--backdrop);
    font-family: "Poppins", sans-serif;
  }
  .canvas { position: relative; width: 1093px; height: 1200px; }

  .card {
    position: absolute; left: 264px; width: 580px; height: 356px;
    border-radius: 24px; overflow: hidden;
  }
  .card--front { top: 226px; background: var(--paper); }
  .card--back {
    top: 621px; width: 584px;
    background: linear-gradient(160deg, var(--night-1) 0%, var(--night-2) 35%, var(--night-3) 60%, var(--night-2) 100%);
  }

  .brand {
    position: absolute; white-space: nowrap;
    font-family: "Poppins", sans-serif; font-weight: 500;
    transform: translate(-50%, -50%);
  }
  .card--front .brand { left: 146px; top: 189px; font-size: 22px; color: var(--orange); }
  .card--back .brand { left: 292px; top: 188px; font-size: 38px; color: var(--orange); }

  .divider {
    position: absolute; left: 290px; top: 74px; width: 2px; height: 209px;
    background: linear-gradient(to bottom, transparent, var(--rule) 15%, var(--rule) 85%, transparent);
  }

  .contact { position: absolute; left: 311px; top: 80px; right: 20px; color: var(--ink); }
  .contact__name {
    font-family: "Open Sans", sans-serif; font-weight: 600;
    font-size: 29px; line-height: 1.1; color: var(--orange);
  }
  .contact__surname { color: var(--blue); }
  .contact__role { font-size: 17px; line-height: 1.1; margin-bottom: 14px; }
  .contact__list { list-style: none; }
  .contact__item {
    display: flex; align-items: center; gap: 7px;
    font-size: 17px; line-height: 21px; white-space: nowrap;
  }
  .contact__item svg { width: 15px; height: 15px; flex: none; margin-left: 1px; }
  .contact__accent { color: var(--orange); }
  .contact__address { font-size: 17px; line-height: 21px; margin-top: 12px; margin-left: 1px; }

  .tagline-band {
    position: absolute; left: 0; bottom: 0; width: 100%; height: 44px;
    background: var(--blue); color: var(--paper);
    font-size: 17px; line-height: 44px; text-align: center;
  }
</style>
</head>
<body>
<main class="canvas">
  <section class="card card--front" aria-label="Business card front">
    <p class="brand">Harborline Benches</p>
    <div class="divider"></div>
    <div class="contact">
      <h1 class="contact__name">Marcus <span class="contact__surname">Hale</span></h1>
      <p class="contact__role">Managing Director</p>
      <ul class="contact__list">
        <li class="contact__item">
          <svg viewBox="0 0 24 24" aria-hidden="true"><path fill="#ec7424" d="M6.6 10.8a15.2 15.2 0 0 0 6.6 6.6l2.2-2.2a1 1 0 0 1 1-.25 11.4 11.4 0 0 0 3.6.57 1 1 0 0 1 1 1V20a1 1 0 0 1-1 1A17 17 0 0 1 3 4a1 1 0 0 1 1-1h3.5a1 1 0 0 1 1 1c0 1.25.2 2.45.57 3.57a1 1 0 0 1-.25 1z"/><path fill="none" stroke="#ec7424" stroke-width="2" d="M14 3a7 7 0 0 1 7 7M14 7a3 3 0 0 1 3 3"/></svg>
          044-123 456 789
        </li>
        <li class="contact__item">
          <svg viewBox="0 0 24 24" aria-hidden="true"><rect x="2" y="5" width="20" height="14" fill="#ec7424"/><path fill="none" stroke="#fff" stroke-width="1.6" d="M2 5l10 8 10-8M2 19l7-7M22 19l-7-7"/></svg>
          info@harborline.com
        </li>
        <li class="contact__item">
          <svg viewBox="0 0 24 24" aria-hidden="true"><g fill="none" stroke="#ec7424" stroke-width="2"><circle cx="12" cy="12" r="10"/><ellipse cx="12" cy="12" rx="4" ry="10"/><path d="M2 12h20M4 7h16M4 17h16"/></g></svg>
          <span>www.<span class="contact__accent">harborline</span>.com</span>
        </li>
      </ul>
      <p class="contact__address">421, Address line goes here<br>45452,Country Name</p>
    </div>
    <p class="tagline-band">Wooden Tables and Furniture of the Highest Quality</p>
  </section>

  <section class="card card--back" aria-label="Business card back">
    <p class="brand">Harborline Benches</p>
  </section>
</main>
</body>
</html>
```